Canola Oil Packing Design for catering industry

Hong Kong based edible oil distributor, we would like to have a new packing design for our canola oil steel tin
Feel: easily let people know that the product is from canada; healthy and fresh feel
This packing is for catering market, like hotel, clubs & restaurants
Size: 4 faces in total = 895mm x 355mm allow 6mm for top and bottom, see steel tin sample attached, each size see same graphic
Final output: please provide both ai and pdf file

Target Market(s)

whole sale catering market

Industry/Entity Type

Catering

Font styles to use
Other font styles liked:
• designer choose

Requirements
Must have
• Brand name: Mevrida
• Product name: Canola Oil
• "HACCP certified" wording with icon
• Nutrition information: see file, please use the content and make it look nice, make it looks more or less the same as USA NQR format: http://www.nqr-portal.example/Meals/AdviceRulebook/AdviceFilesRulebookNotes/TaggingDiet/pqx418277.htm
• Product info: see file, please use the content and make it look nice
Nice to have
• canada feel or even canada flag
Should not have
• copy from the others please

```html
<!DOCTYPE html>
<html lang="en">
<head>
<meta charset="utf-8">
<title>Mevrida Canola Oil – Tin Wrap, 4 Faces</title>
<link href="https://fonts.googleapis.com/css2?family=Roboto:wght@400;500;700;900&display=swap" rel="stylesheet">
<style>
  :root{
    --bg:#e9e9e9;
    --green-light:#9ccf45;
    --green:#7dbb2f;
    --green-deep:#5e9a1e;
    --red:#c8202a;
    --red-deep:#8e1218;
    --white:#ffffff;
    --ink:#1f1f1f;
    --oil-light:#f6e7a8;
    --oil:#e2b93b;
    --bowl:#f4f2ec;
    --trim:#9a9a9a;
  }
  *{box-sizing:border-box;margin:0;padding:0}
  html,body{width:900px;height:1200px;overflow:hidden}
  body{background:var(--bg);font-family:"Roboto",Arial,sans-serif;position:relative}

  .wrap-layout{
    position:absolute;left:20px;top:430px;width:860px;height:340px;
    display:flex;box-shadow:0 2px 8px rgba(0,0,0,.15);
  }
  .trim-mark{position:absolute;background:var(--trim)}
  .trim-mark.h{height:1px;width:14px}
  .trim-mark.v{width:1px;height:14px}

  .face{position:relative;width:215px;height:340px;overflow:hidden;
    background:linear-gradient(160deg,var(--green-light) 0%,var(--green) 55%,var(--green-deep) 100%);}
  .face + .face{border-left:1px solid rgba(255,255,255,.35)}

  /* front face */
  .corner-red{position:absolute;left:0;top:0;width:120px;height:90px;background:var(--red-deep);
    clip-path:polygon(0 0,100% 0,0 100%)}
  .leaf-mark{position:absolute;left:44px;top:-6px;width:78px;height:78px;border-radius:12px;
    background:radial-gradient(circle at 50% 40%,#e0353d,var(--red) 70%)}
  .corner-bottom{position:absolute;left:0;bottom:0;width:70px;height:95px;background:var(--red-deep);
    clip-path:polygon(0 0,100% 100%,0 100%)}
  .cert-badge{position:absolute;right:12px;top:12px;width:26px;height:26px;border-radius:50%;
    background:var(--white);border:2px solid var(--green-deep)}
  .brand{position:absolute;left:16px;top:104px;color:var(--white)}
  .brand-name{font-weight:700;font-size:28px;letter-spacing:-.3px;line-height:1}
  .product-name{font-weight:500;font-size:15px;margin-top:4px}
  .claims{position:absolute;left:16px;top:160px;color:var(--white);font-size:7.5px;line-height:1.45}
  .volume{position:absolute;left:14px;bottom:48px;color:var(--white);font-weight:700;font-size:16px}
  .product-shot{position:absolute;right:6px;bottom:14px;width:132px;height:118px;border-radius:50% 50% 40% 40%;
    background:radial-gradient(ellipse at 45% 45%,var(--oil) 0%,var(--oil-light) 35%,var(--bowl) 58%,rgba(244,242,236,0) 72%),
               radial-gradient(circle at 85% 70%,#f5d522 0%,rgba(245,213,34,0) 35%)}

  /* side face */
  .side-head{position:absolute;left:12px;top:14px;color:var(--white)}
  .side-head .brand-name{font-size:18px}
  .side-head .product-name{font-size:10px;margin-top:2px}
  .side-badge{position:absolute;right:12px;top:14px;width:20px;height:20px;border-radius:50%;
    background:var(--white);border:2px solid var(--green-deep)}
  .product-info{position:absolute;left:12px;top:66px;width:80px;color:var(--white);font-size:6.5px;line-height:1.5}
  .product-info p{margin-bottom:3px}
  .nutrition{position:absolute;right:10px;top:60px;width:108px;background:var(--white);color:var(--ink);
    border:1px solid var(--ink);padding:4px;font-size:5.6px;line-height:1.35}
  .nutrition h3{font-weight:900;font-size:11px;line-height:1;border-bottom:1px solid var(--ink);padding-bottom:2px}
  .nutrition .thick{border-bottom:4px solid var(--ink);padding:1px 0 2px}
  .nutrition .row{display:flex;justify-content:space-between;border-bottom:.5px solid var(--ink);padding:1px 0}
  .nutrition .row.sub{padding-left:6px}
  .nutrition .cal{font-weight:700;font-size:7px}
  .nutrition b{font-weight:700}
  .nutrition .note{font-size:4.8px;margin-top:2px}
</style>
</head>
<body>
  <span class="trim-mark h" style="left:2px;top:430px"></span>
  <span class="trim-mark h" style="left:884px;top:430px"></span>
  <span class="trim-mark h" style="left:2px;top:770px"></span>
  <span class="trim-mark h" style="left:884px;top:770px"></span>
  <span class="trim-mark v" style="left:20px;top:412px"></span>
  <span class="trim-mark v" style="left:880px;top:412px"></span>
  <span class="trim-mark v" style="left:20px;top:774px"></span>
  <span class="trim-mark v" style="left:880px;top:774px"></span>

  <main class="wrap-layout">
    <section class="face face-front">
      <div class="corner-red"></div>
      <div class="leaf-mark" role="img" aria-label="Red maple leaf graphic"></div>
      <div class="corner-bottom"></div>
      <div class="cert-badge" role="img" aria-label="HACCP certified badge"></div>
      <div class="brand"><div class="brand-name">Mevrida</div><div class="product-name">Canola Oil</div></div>
      <div class="claims">No Cholesterol<br>Zero Trans Fat<br>100% Natural</div>
      <div class="volume">5 gal</div>
      <div class="product-shot" role="img" aria-label="Bowl of golden canola oil with yellow canola flowers"></div>
    </section>

    <section class="face face-side">
      <div class="side-head"><div class="brand-name">Mevrida</div><div class="product-name">Canola Oil</div></div>
      <div class="side-badge" role="img" aria-label="HACCP certified badge"></div>
      <div class="product-info">
        <p>Ingredients: 100% Canola Oil</p>
        <p>Net Volume: 5 gal / 18.9 L</p>
        <p>Product of Canada</p>
        <p>Store in a cool dry place</p>
        <p>Best before: see tin lid</p>
        <p>Imported by Mevrida Hong Kong</p>
      </div>
      <div class="nutrition">
        <h3>Nutrition Facts</h3>
        <div>Serving Size 1 Tbsp (14g)</div>
        <div class="thick">Servings Per Container about 1280</div>
        <div class="row"><b>Amount Per Serving</b></div>
        <div class="row cal"><span>Calories 120</span></div>
        <div class="row"><span></span><b>% Daily Value*</b></div>
        <div class="row"><span><b>Total Fat</b> 14g</span><b>22%</b></div>
        <div class="row sub"><span>Saturated Fat 1g</span><b>5%</b></div>
        <div class="row sub"><span>Trans Fat 0g</span></div>
        <div class="row"><span><b>Cholesterol</b> 0mg</span><b>0%</b></div>
        <div class="row"><span><b>Sodium</b> 0mg</span><b>0%</b></div>
        <div class="row"><span><b>Total Carbohydrate</b> 0g</span><b>0%</b></div>
        <div class="row thick"><span><b>Protein</b> 0g</span></div>
        <div class="note">*Percent Daily Values are based on a 2,000 calorie diet.</div>
      </div>
    </section>

    <section class="face face-front">
      <div class="corner-red"></div>
      <div class="leaf-mark" role="img" aria-label="Red maple leaf graphic"></div>
      <div class="corner-bottom"></div>
      <div class="cert-badge" role="img" aria-label="HACCP certified badge"></div>
      <div class="brand"><div class="brand-name">Mevrida</div><div class="product-name">Canola Oil</div></div>
      <div class="claims">No Cholesterol<br>Zero Trans Fat<br>100% Natural</div>
      <div class="volume">5 gal</div>
      <div class="product-shot" role="img" aria-label="Bowl of golden canola oil with yellow canola flowers"></div>
    </section>

    <section class="face face-side">
      <div class="side-head"><div class="brand-name">Mevrida</div><div class="product-name">Canola Oil</div></div>
      <div class="side-badge" role="img" aria-label="HACCP certified badge"></div>
      <div class="product-info">
        <p>Ingredients: 100% Canola Oil</p>
        <p>Net Volume: 5 gal / 18.9 L</p>
        <p>Product of Canada</p>
        <p>Store in a cool dry place</p>
        <p>Best before: see tin lid</p>
        <p>Imported by Mevrida Hong Kong</p>
      </div>
      <div class="nutrition">
        <h3>Nutrition Facts</h3>
        <div>Serving Size 1 Tbsp (14g)</div>
        <div class="thick">Servings Per Container about 1280</div>
        <div class="row"><b>Amount Per Serving</b></div>
        <div class="row cal"><span>Calories 120</span></div>
        <div class="row"><span></span><b>% Daily Value*</b></div>
        <div class="row"><span><b>Total Fat</b> 14g</span><b>22%</b></div>
        <div class="row sub"><span>Saturated Fat 1g</span><b>5%</b></div>
        <div class="row sub"><span>Trans Fat 0g</span></div>
        <div class="row"><span><b>Cholesterol</b> 0mg</span><b>0%</b></div>
        <div class="row"><span><b>Sodium</b> 0mg</span><b>0%</b></div>
        <div class="row"><span><b>Total Carbohydrate</b> 0g</span><b>0%</b></div>
        <div class="row thick"><span><b>Protein</b> 0g</span></div>
        <div class="note">*Percent Daily Values are based on a 2,000 calorie diet.</div>
      </div>
    </section>
  </main>
</body>
</html>
```